Modern Business Card for Larkwell 2018

Our company assumes the best about people. We are creating an online community of entrepreneurs and business leaders who struggle with marketing their business online.

This business card should POP! We recently got a new logo and are launching a new website next month, so our business cards should make a statement that feels:
-Fresh
-Smart
-Trustworthy
-Fun

Target Market(s)

small business owners, entrepreneurs

Industry/Entity Type

Digital Marketing

Contact Information for Business Card

Dimensions: 3.5" x 2"

Font styles to use
Sans Serif

Colors
f37122
ffffff

Requirements
Must have
• We need a business card with a modern, bold design. We will use one side of the card as a lead-generation offer, so text on one side will need to fit up to 140 characters. The business card should stick to our core colors (orange, black, and white).
Nice to have
• We think a vertical "portrait" design could be interesting.
Should not have
• Should not look like a traditional business card. The round icon should stand out from a distance.

```html
<!DOCTYPE html>
<html lang="en">
<head>
<meta charset="utf-8">
<title>Larkwell Business Card</title>
<link rel="stylesheet" href="https://fonts.googleapis.com/css2?family=Open+Sans:wght@400;600;700;800&display=swap">
<style>
  :root {
    --orange: #f37122;
    --ink: #2b2b2b;
    --white: #ffffff;
    --paper: #f7f7f5;
    --backdrop: #e9e6e1;
    --rule: rgba(255, 255, 255, 0.55);
    --line-grey: #8a8a8a;
  }
  * { box-sizing: border-box; margin: 0; padding: 0; }
  html, body {
    width: 1200px;
    height: 950px;
    overflow: hidden;
  }
  body {
    background: var(--backdrop);
    font-family: "Open Sans", Arial, sans-serif;
    position: relative;
  }
  .card {
    position: absolute;
    left: 250px;
    width: 700px;
    height: 400px;
    border-radius: 4px;
    overflow: hidden;
    box-shadow: 0 10px 24px rgba(0, 0, 0, 0.18);
  }
  .card--front { top: 50px; background: var(--white); }
  .card--back { top: 500px; background: var(--orange); }

  /* Front */
  .front-swoosh {
    position: absolute;
    inset: 0;
    width: 700px;
    height: 400px;
  }
  .brand {
    position: absolute;
    display: flex;
    flex-direction: column;
  }
  .brand__name {
    font-weight: 800;
    font-size: 56px;
    line-height: 1;
    letter-spacing: 1px;
    text-transform: uppercase;
    color: var(--ink);
  }
  .brand__tagline {
    font-weight: 700;
    font-size: 13px;
    letter-spacing: 1.2px;
    text-transform: uppercase;
    color: var(--ink);
    margin-top: 8px;
  }
  .card--front .brand { left: 340px; top: 96px; }

  .contact {
    position: absolute;
    left: 40px;
    bottom: 38px;
    color: var(--white);
  }
  .contact__name {
    font-weight: 700;
    font-size: 27px;
    text-transform: uppercase;
    letter-spacing: 0.5px;
    line-height: 1.15;
  }
  .contact__role {
    font-weight: 600;
    font-size: 20px;
    text-transform: uppercase;
    line-height: 1.3;
  }
  .contact__email {
    font-weight: 400;
    font-size: 18px;
    line-height: 1.4;
  }

  /* Back */
  .card--back .brand {
    left: 40px;
    top: 70px;
    width: 360px;
    align-items: center;
  }
  .card--back .brand__name,
  .card--back .brand__tagline { color: var(--white); }

  .back-divider {
    position: absolute;
    left: 420px;
    top: 28px;
    width: 1px;
    height: 190px;
    background: var(--rule);
  }
  .offer {
    position: absolute;
    left: 446px;
    top: 30px;
    width: 236px;
    color: var(--white);
  }
  .offer__headline {
    font-weight: 800;
    font-size: 19px;
    line-height: 1.12;
    text-transform: uppercase;
  }
  .offer__body {
    font-weight: 400;
    font-size: 14.5px;
    line-height: 1.35;
    margin-top: 12px;
  }
  .offer__link {
    font-weight: 700;
    font-size: 17px;
    margin-top: 10px;
  }
  .note-panel {
    position: absolute;
    left: 24px;
    right: 24px;
    top: 246px;
    height: 128px;
    background: var(--paper);
    border-radius: 14px;
  }
  .note-panel__line {
    position: absolute;
    left: 18px;
    right: 18px;
    height: 1px;
    background: var(--line-grey);
  }
  .note-panel__line:nth-child(1) { top: 42px; }
  .note-panel__line:nth-child(2) { top: 86px; }
</style>
</head>
<body>

  <section class="card card--front" aria-label="Card front">
    <svg class="front-swoosh" viewBox="0 0 700 400" aria-hidden="true">
      <path d="M0,150 C210,300 440,336 700,318 L700,330 C430,346 190,316 0,176 Z" fill="var(--ink)"/>
      <path d="M0,176 C190,316 430,346 700,330 L700,400 L0,400 Z" fill="var(--orange)"/>
    </svg>

    <div class="brand">
      <span class="brand__name">Larkwell</span>
      <span class="brand__tagline">Marketing that moves people</span>
    </div>

    <div class="contact">
      <p class="contact__name">Dana Mercer</p>
      <p class="contact__role">Story Marketing Coach</p>
      <p class="contact__email">dana@larkwellnow.com</p>
    </div>
  </section>

  <section class="card card--back" aria-label="Card back">
    <div class="brand">
      <span class="brand__name">Larkwell</span>
      <span class="brand__tagline">Marketing that moves people</span>
    </div>

    <span class="back-divider"></span>

    <div class="offer">
      <p class="offer__headline">Reach more people.<br>Make more money.<br>Create more impact.</p>
      <p class="offer__body">Get your free Larkwell Starter Package and our marketing guide today at</p>
      <p class="offer__link">larkwellnow.com/start</p>
    </div>

    <div class="note-panel">
      <span class="note-panel__line"></span>
      <span class="note-panel__line"></span>
    </div>
  </section>

</body>
</html>
```